FinTech company looking to revamp and expand client-facing interface for our financial models

Pellworth Engines currently has a very simple website that allows clients to interact with our financial models. We are looking to completely redesign the current site and add several extra pages to provide extra functionality. We want the design to have a modern, slick feel, that will work on both a desktop or a tablet. It should be straightforward for clients to move between different pages at any time, and clear from the layout how to interact with the more advanced features. We have included screenshots of existing pages in the attached design brief, as well as sketches of the functionality required by the new pages, but can't provide a direct link to the current site.
Target Market(s)
Professional investors that will be paying to access the interface
Industry/Entity Type
Finance
Number of Pages Required
4 page
Colors
Designer to choose colors to be used in the design.
Look and feel
Each slider illustrates characteristics of the customer's brand and the style your logo design should communicate.

```html
<!DOCTYPE html>
<html lang="en">
<head>
<meta charset="utf-8">
<title>Pellworth – ETF Pairs Models</title>
<link rel="stylesheet" href="https://fonts.googleapis.com/css2?family=Montserrat:wght@500;600;700&family=Open+Sans:wght@400;600;700&family=Roboto:wght@400;500&display=swap">
<style>
:root{
  --page:#e6e6e6;
  --surface:#ffffff;
  --navy:#0a3366;
  --ink:#111111;
  --teal:#066f6b;
  --row-alt:#f0f0f0;
  --line:#dcdcdc;
  --veil:rgba(196,196,196,0.82);
  --panel-head:#666666;
  --tab:#ffffff;
  --tab-active:#1b1b1b;
}
*{box-sizing:border-box;margin:0;padding:0}
html,body{width:1200px;height:706px;overflow:hidden;background:var(--page)}
.canvas{position:relative;width:1200px;height:706px;background:var(--page);font-family:"Open Sans",sans-serif;color:var(--ink)}
.frame{position:absolute;left:14px;top:14px;width:1172px;height:678px;background:linear-gradient(#ececec 0,#f1f1f1 150px,#fafafa 100%);overflow:hidden}
.topbar{position:absolute;left:0;top:0;width:1172px;height:55px;background:var(--surface);box-shadow:0 3px 8px rgba(0,0,0,.08);font-family:"Montserrat",sans-serif}
.brand{position:absolute;left:42px;top:0;line-height:55px;font-weight:700;font-size:16px;letter-spacing:.2px}
.period,.section{position:absolute;top:0;height:55px;display:flex;align-items:center;justify-content:center;font-size:13px;font-weight:700;border-right:1px solid #eee;gap:8px}
.period.is-active,.section.is-active{background:var(--navy);color:#fff}
.section svg{width:22px;height:22px}
.subtab{position:absolute;display:flex;align-items:center;justify-content:center;background:var(--tab);font-size:12.5px;font-weight:600;color:#333;border-radius:4px 4px 0 0;box-shadow:0 -1px 4px rgba(0,0,0,.05)}
.subtab.is-active{background:var(--tab-active);color:#fff}
.tab-next{position:absolute;left:1084px;top:111px;width:37px;height:32px;background:#fff;display:flex;align-items:center;justify-content:center}
.tab-add{position:absolute;left:1126px;top:111px;width:37px;height:32px;background:var(--navy);display:flex;align-items:center;justify-content:center}
.export{position:absolute;left:1061px;top:194px;display:flex;align-items:center;gap:8px;font-family:"Montserrat",sans-serif;font-weight:600;font-size:16px;color:var(--navy)}
.models{position:absolute;left:83px;top:217px;width:1071px;border-collapse:collapse;background:#fff;font-family:"Roboto",sans-serif;font-size:15px;box-shadow:0 2px 8px rgba(0,0,0,.08);border-radius:6px;overflow:hidden}
.models th{background:var(--teal);color:#fff;font-family:"Montserrat",sans-serif;font-weight:600;font-size:15.5px;height:65px;border-right:1px solid rgba(255,255,255,.2)}
.models td{height:65px;text-align:center;border-right:1px solid var(--line);line-height:1.25}
.models tr:nth-child(even) td{background:var(--row-alt)}
.models td:nth-child(-n+3){font-size:14.5px}
.veil{position:absolute;left:0;top:143px;width:452px;height:397px;background:var(--veil)}
.filter-handle{position:absolute;left:397px;top:226px;width:101px;height:231px;background:rgba(190,190,190,.85);border-radius:0 4px 4px 0}
.filter-handle .label{position:absolute;left:60px;top:150px;transform:rotate(-90deg);transform-origin:0 0;font-family:"Montserrat",sans-serif;font-weight:700;font-size:14px;letter-spacing:1px;color:var(--ink)}
.filter-handle .toggle{position:absolute;left:90px;top:103px;width:22px;height:22px;border-radius:50%;background:var(--navy);border:2px solid #fff;display:flex;align-items:center;justify-content:center}
.filters{position:absolute;left:55px;top:212px;width:342px;height:259px;background:#fff;border-radius:4px;overflow:hidden;box-shadow:0 2px 10px rgba(0,0,0,.12)}
.filters h2{height:46px;line-height:46px;text-align:center;background:var(--panel-head);color:#fff;font-size:16px;font-weight:600}
.filter-row{height:48px;display:flex;align-items:center;padding-left:15px;border-bottom:1px solid #eee;font-size:15.5px}
.filter-row b{font-weight:700}
.filter-row .name{width:80px}
.filter-row .field{margin-left:10px;width:140px;height:28px;border:1px solid #ccc;border-radius:5px;box-shadow:inset 0 1px 3px rgba(0,0,0,.1);padding-left:12px;line-height:26px;font-size:15px}
.apply{height:45px;display:flex;align-items:center;padding-left:15px;gap:14px;font-size:15.5px;font-weight:600;border-bottom:1px solid #eee}
.check{display:flex;align-items:center;gap:8px}
.check i{display:block;width:17px;height:17px;border:1px solid #aaa;border-radius:3px;background:#f5f5f5}
.search{position:absolute;left:101px;top:201px;width:141px;height:45px;background:var(--navy);color:#fff;border-radius:3px;font-weight:600;font-size:14.5px;display:flex;align-items:center;justify-content:center}
</style>
</head>
<body>
<div class="canvas">
 <div class="frame">
  <header class="topbar">
   <div class="brand">PELLWORTH</div>
   <div class="period is-active" style="left:166px;width:83px">250D</div>
   <div class="period" style="left:249px;width:83px">83D</div>
   <div class="period" style="left:332px;width:83px">42D</div>
   <div class="period" style="left:415px;width:1px;border-right:1px solid #eee"></div>
   <div class="section is-active" style="left:540px;width:131px">
    <svg viewBox="0 0 24 24" fill="none" stroke="#fff" stroke-width="2"><path d="M3 11 12 3l9 8"/><path d="M5 9.5V21h5v-6h4v6h5V9.5"/></svg>MODELS</div>
   <div class="section" style="left:671px;width:162px">
    <svg viewBox="0 0 24 24" fill="#222"><circle cx="12" cy="12" r="3"/><circle cx="12" cy="3" r="1.4"/><circle cx="12" cy="21" r="1.4"/><circle cx="3" cy="12" r="1.4"/><circle cx="21" cy="12" r="1.4"/><circle cx="5.6" cy="5.6" r="1.4"/><circle cx="18.4" cy="18.4" r="1.4"/><circle cx="5.6" cy="18.4" r="1.4"/><circle cx="18.4" cy="5.6" r="1.4"/><circle cx="12" cy="7.5" r="1"/><circle cx="12" cy="16.5" r="1"/><circle cx="7.5" cy="12" r="1"/><circle cx="16.5" cy="12" r="1"/></svg>SENSITIVITIES</div>
   <div class="section" style="left:833px;width:148px">
    <svg viewBox="0 0 24 24" fill="none" stroke="#222" stroke-width="1.8"><circle cx="7" cy="7" r="4"/><circle cx="17" cy="7" r="4"/><circle cx="7" cy="17" r="4"/><circle cx="17" cy="17" r="4"/></svg>PORTFOLIO</div>
   <div class="section" style="left:981px;width:140px">
    <svg viewBox="0 0 24 24" fill="none" stroke="#222" stroke-width="1.8"><rect x="2.5" y="3.5" width="19" height="17"/><path d="M5 16l4-5 3 3 4-6 3 3"/></svg>BACKTEST</div>
  </header>

  <nav>
   <div class="subtab" style="left:51px;top:111px;width:143px;height:32px">EQUITIES</div>
   <div class="subtab" style="left:198px;top:111px;width:143px;height:32px">ETFS</div>
   <div class="subtab" style="left:346px;top:101px;width:143px;height:42px">PAIRS</div>
   <div class="subtab is-active" style="left:494px;top:92px;width:143px;height:51px">ETF PAIRS</div>
   <div class="subtab" style="left:641px;top:101px;width:143px;height:42px">FACTORS</div>
   <div class="subtab" style="left:789px;top:111px;width:143px;height:32px">NEW TAB TITLE #1</div>
   <div class="subtab" style="left:937px;top:111px;width:143px;height:32px">NEW TAB TITLE #2</div>
   <div class="tab-next"><svg width="12" height="18" viewBox="0 0 12 18"><path d="M2 2l7 7-7 7" fill="none" stroke="#777" stroke-width="3"/></svg></div>
   <div class="tab-add"><svg width="22" height="22" viewBox="0 0 22 22" fill="none" stroke="#fff" stroke-width="1.8"><circle cx="11" cy="11" r="9.5"/><path d="M11 6v10M6 11h10"/></svg></div>
  </nav>

  <div class="export"><svg width="24" height="22" viewBox="0 0 24 22" fill="none" stroke="#0a3366" stroke-width="2.2"><path d="M10 4H3v16h16v-6"/><path d="M9 14c1-6 5-9 12-9"/><path d="M16 1l5 4-4 5"/></svg>Export</div>

  <table class="models">
   <colgroup><col style="width:92px"><col style="width:129px"><col style="width:107px"><col style="width:78px"><col style="width:83px"><col style="width:83px"><col style="width:83px"><col style="width:83px"><col style="width:83px"><col style="width:84px"><col style="width:83px"><col style="width:83px"></colgroup>
   <thead><tr><th>Model</th><th>Sector</th><th>Time</th><th>Quality</th><th>Stat 1</th><th>Stat 2</th><th>Stat 3</th><th>Stat 4</th><th>Stat 5</th><th>Stat 6</th><th>Stat 7</th><th>Stat 8</th></tr></thead>
   <tbody>
    <tr><td>Model 1</td><td>Information<br>Technology</td><td>2019-07-03<br>12:15:00.000</td><td>30.2281</td><td>2.01574</td><td>23.305</td><td>-0.149368</td><td>22.3054</td><td>4.63714</td><td>0.945706</td><td>2.81949</td><td>2.60858</td></tr>
    <tr><td>Model 2</td><td>Information<br>Technology</td><td>2019-07-03<br>12:15:00.000</td><td>32.8694</td><td>0.87307</td><td>32.185</td><td>-0.033692</td><td>33.9911</td><td>11.5693</td><td>-0.472968</td><td>-0.830458</td><td>6.80646</td></tr>
    <tr><td>Model 3</td><td>Information<br>Technology</td><td>2019-07-03<br>12:15:00.000</td><td>1.66002</td><td>-0.569222</td><td>159.814</td><td>0.0252328</td><td>172.616</td><td>10.2875</td><td>-0.750396</td><td>-0.385309</td><td>4.69146</td></tr>
    <tr><td>Model 4</td><td>Information<br>Technology</td><td>2019-07-03<br>12:15:00.000</td><td>45.6856</td><td>0.412148</td><td>202.488</td><td>0.0084923</td><td>205.834</td><td>11.9094</td><td>-0.137913</td><td>0.449595</td><td>3.85106</td></tr>
    <tr><td>Model 5</td><td>Information<br>Technology</td><td>2019-07-03<br>12:15:00.000</td><td>75.7733</td><td>7.06728</td><td>188.605</td><td>0.016913</td><td>161.665</td><td>3.82241</td><td>0.981019</td><td>1.29847</td><td>3.34927</td></tr>
   </tbody>
  </table>

  <div class="veil"></div>
  <div class="filter-handle">
   <span class="label">FILTERS</span>
   <span class="toggle"><svg width="12" height="10" viewBox="0 0 12 10" fill="none" stroke="#fff" stroke-width="1.8"><path d="M11 5H2M5.5 1.5 2 5l3.5 3.5"/></svg></span>
  </div>

  <section class="filters">
   <h2>Filters</h2>
   <div class="filter-row"><span class="name">Quality</span><b>Threshold:</b><span class="field">-10</span></div>
   <div class="filter-row"><span class="name"><b>Abs.</b> Stat</span><b>Threshold:</b><span class="field">-10</span></div>
   <div class="apply">Apply <span class="check"><i></i>All tabs</span><span class="check"><i></i>Current tab</span></div>
   <div class="search">SEARCH</div>
  </section>
 </div>
</div>
</body>
</html>
```